Professional violinist needs business cards

I am trying to attract the following jobs:
-private violin lessons (primarily classical)
-performance gigs (weddings, birthday parties, funerals, etc.)
-collaborations with other artists (studio recordings, performances)

I want to communicate that I have a very high standard of excellence for my work, but I also love people and celebrations.
Values/style words I like are:
love, joy, peace, fun, beauty, authenticity, excellence, warmth, refined/sleek, free spirited. If that's too confusing, just ignore :)

I will attach my favorite business card template that I could find on Canva. The lines are supposed to be like a music staff, which I think is really cool, but I also don't want it to look too busy. I like the simple black and white--I think it looks sharp--but I also am open to other ideas. I also have seen business cards with pictures included that looked great, so I attached an image that could be used as well.

I am also attaching a file that I made of my initials that could be used as a logo, but I'm not sure if it should be included.

Information on the card:
-My name (18 letters total)
-"violinist"
-phone number, email, website

Thank you!

```html
<!DOCTYPE html>
<html lang="en">
<head>
<meta charset="utf-8">
<title>Marianne Holloway – Violinist Business Cards</title>
<link rel="stylesheet" href="https://fonts.googleapis.com/css2?family=Dancing+Script:wght@500&family=Crimson+Text:wght@400&family=Cinzel:wght@400&display=swap">
<style>
  :root {
    --backdrop: #2a2a2b;
    --card: #22262a;
    --card-edge: #1b1e21;
    --gold: #c8b48c;
    --ivory: #ebe8e2;
    --silver: #dcdcdc;
    --photo-stone: #6e6656;
    --photo-dark: #2c2924;
  }
  * { margin: 0; padding: 0; box-sizing: border-box; }
  html, body { width: 1200px; height: 1138px; overflow: hidden; }
  body { background: var(--backdrop); position: relative; }

  .card {
    position: absolute;
    left: 275px;
    width: 620px;
    height: 374px;
    background: var(--card);
    border-radius: 14px;
    overflow: hidden;
  }
  .card--front { top: 186px; }
  .card--back { top: 608px; }

  .front-accent {
    position: absolute;
    left: -70px;
    top: 120px;
    width: 180px;
    height: 180px;
    border-radius: 50%;
    background: var(--silver);
  }

  .brand-block {
    position: absolute;
    text-align: center;
    transform: translateX(-50%);
  }
  .card--front .brand-block { left: 375px; top: 110px; width: 360px; }
  .card--back .brand-block { left: 432px; top: 70px; width: 320px; }

  .monogram-name {
    font-family: "Crimson Text", serif;
    font-size: 22px;
    color: var(--gold);
    letter-spacing: 1px;
    line-height: 1;
  }
  .artist-name {
    font-family: "Dancing Script", cursive;
    font-weight: 500;
    color: var(--ivory);
    line-height: 1;
  }
  .card--front .artist-name { font-size: 40px; margin-top: 44px; }
  .card--back .artist-name { font-size: 34px; margin-top: 36px; }

  .role {
    display: flex;
    align-items: center;
    justify-content: center;
    gap: 18px;
    font-family: "Cinzel", serif;
    color: var(--ivory);
    letter-spacing: 2.5px;
  }
  .card--front .role { font-size: 17px; margin-top: 14px; }
  .card--back .role { font-size: 15px; margin-top: 12px; }
  .role .rule { height: 1px; background: var(--gold); }
  .card--front .role .rule { width: 82px; }
  .card--back .role .rule { width: 70px; }

  .photo {
    position: absolute;
    left: 0; top: 0;
    width: 242px; height: 100%;
    background: linear-gradient(90deg, var(--photo-stone) 0%, #5a5346 60%, var(--photo-dark) 100%);
  }
  .photo::after {
    content: "";
    position: absolute;
    right: 0; top: 0;
    width: 40px; height: 100%;
    background: linear-gradient(90deg, rgba(34,38,42,0), var(--card));
  }

  .contact {
    position: absolute;
    left: 432px;
    top: 226px;
    transform: translateX(-50%);
    list-style: none;
    text-align: center;
    font-family: "Crimson Text", serif;
    font-size: 15px;
    line-height: 23.5px;
    color: var(--ivory);
    white-space: nowrap;
  }
  .contact .highlight { color: var(--gold); }
</style>
</head>
<body>
  <section class="card card--front">
    <div class="front-accent"></div>
    <div class="brand-block">
      <div class="monogram-name">M. Holloway</div>
      <div class="artist-name">Marianne Holloway</div>
      <div class="role"><span class="rule"></span>VIOLINIST<span class="rule"></span></div>
    </div>
  </section>

  <section class="card card--back">
    <div class="photo" role="img" aria-label="Portrait photo of the violinist in a black dress holding a violin and bow beside a stone wall"></div>
    <div class="brand-block">
      <div class="monogram-name">M. Holloway</div>
      <div class="artist-name">Marianne Holloway</div>
      <div class="role"><span class="rule"></span>VIOLINIST<span class="rule"></span></div>
    </div>
    <ul class="contact">
      <li>+1 (555) 014-2290</li>
      <li>marianne@mariannehollowaymusic.com</li>
      <li>www.<span class="highlight">MarianneHollowayMusic</span>.com</li>
      <li>Portland, OR</li>
    </ul>
  </section>
</body>
</html>
```